Corvane Paintless Dent Removal

Our company works on vehicles removing dents using a highly skilled trade which the metal is massaged out with special tools without disturbing the original paint, hence paintless dent removal. Besides keeping the paint and metal original its also very environmentally friendly since no paint or toxic fillers are used. Also we we are one of the most experienced companies in the business with 25 years

Target Market(s)

Retail Automobile consumers, Auto Dealerships and Auto Body Shops

Industry/Entity Type

Auto Repair

Contact Information for Business Card

Dale Hollister
PO Box 518 Brookmere, NY 11962
631-555-0148
corvanepdr@mailbox-example.com
website corvanepdr.example
youtube corvane paintless dent removal
25 years of experience removing Dents, Dings and Hail Damage

Font styles to use
Serif
Sans Serif

Colors

Designer to choose colors to be used in the design.

Requirements
Must have
• I do like things that are simple but classy and somewhat bold, also I like my logo so that should be somewhat important

```html
<!DOCTYPE html>
<html lang="en">
<head>
<meta charset="utf-8">
<title>Corvane Paintless Dent Removal – Business Card</title>
<link rel="stylesheet" href="https://fonts.googleapis.com/css2?family=Roboto:wght@400;700&family=Roboto+Condensed:wght@700&display=swap">
<style>
  :root {
    --navy: #13284d;
    --navy-deep: #10264a;
    --card-white: #f3f3f3;
    --ink: #4a4a4a;
    --gold: #d9a322;
    --stage: #e4e2df;
    --white: #ffffff;
  }
  * { margin: 0; padding: 0; box-sizing: border-box; }
  html, body {
    width: 1200px; height: 960px; overflow: hidden;
    background: var(--stage);
    font-family: "Roboto", Arial, sans-serif;
  }
  .canvas { position: relative; width: 1200px; height: 960px; }

  .card {
    position: absolute;
    box-shadow: 0 2px 6px rgba(0,0,0,0.25);
  }
  .card-front {
    left: 314px; top: 113px; width: 600px; height: 343px;
    background: var(--card-white);
  }
  .card-back {
    left: 311px; top: 472px; width: 601px; height: 343px;
    background: var(--navy-deep);
  }

  .brand-name {
    font-family: "Roboto", Arial, sans-serif;
    font-weight: 700;
    line-height: 1;
  }
  .brand-name .brand-main { display: block; font-size: 40px; letter-spacing: 0.5px; }
  .brand-name .brand-sub { display: block; font-size: 15px; margin-top: 4px; }

  .card-front .brand-name {
    position: absolute; left: 58px; top: 62px;
    color: var(--navy);
  }

  .experience-seal {
    position: absolute; left: 502px; top: 25px;
    width: 74px; height: 74px; border-radius: 50%;
    background: var(--gold);
  }

  .contact {
    position: absolute; left: 55px; top: 179px;
    color: var(--ink); font-size: 14px; line-height: 19px;
  }
  .contact .address { margin-bottom: 6px; }
  .contact ul { list-style: none; }
  .contact li { display: flex; align-items: center; gap: 8px; height: 19px; }
  .contact svg { width: 14px; height: 14px; flex: none; fill: var(--navy); }

  .holder-name {
    position: absolute; right: 61px; top: 228px;
    font-family: "Roboto Condensed", "Arial Narrow", sans-serif;
    font-weight: 700; font-size: 21px; color: var(--navy);
    text-transform: uppercase;
  }

  .card-back .brand-name {
    position: absolute; left: 0; right: 0; top: 140px;
    text-align: center; color: var(--white);
  }
  .web-address {
    position: absolute; left: 0; right: 0; top: 280px;
    text-align: center; color: var(--white);
    font-size: 14px; letter-spacing: 5px;
  }
</style>
</head>
<body>
<main class="canvas">

  <section class="card card-front">
    <div class="brand-name">
      <span class="brand-main">CORVANE</span>
      <span class="brand-sub">Paintless Dent Removal</span>
    </div>

    <div class="experience-seal" role="img" aria-label="25 years of experience seal"></div>

    <div class="contact">
      <p class="address">PO Box 518<br>Brookmere, NY 11962</p>
      <ul>
        <li>
          <svg viewBox="0 0 24 24" aria-hidden="true"><path d="M6.6 10.8a15.1 15.1 0 0 0 6.6 6.6l2.2-2.2a1 1 0 0 1 1-.25 11.4 11.4 0 0 0 3.6.57 1 1 0 0 1 1 1V20a1 1 0 0 1-1 1A17 17 0 0 1 3 4a1 1 0 0 1 1-1h3.5a1 1 0 0 1 1 1c0 1.25.2 2.45.57 3.57a1 1 0 0 1-.25 1z"/></svg>
          631-555-0148
        </li>
        <li>
          <svg viewBox="0 0 24 24" aria-hidden="true"><path d="M2 5h20v14H2z M3 6l9 7 9-7" fill="none" stroke="#13284d" stroke-width="2.4"/></svg>
          corvanepdr@mailbox-example.com
        </li>
        <li>
          <svg viewBox="0 0 24 24" aria-hidden="true"><circle cx="12" cy="12" r="9" fill="none" stroke="#13284d" stroke-width="2.4"/><path d="M3 12h18M12 3c3 3 3 15 0 18M12 3c-3 3-3 15 0 18" fill="none" stroke="#13284d" stroke-width="1.8"/></svg>
          corvanepdr.example
        </li>
        <li>
          <svg viewBox="0 0 24 24" aria-hidden="true"><rect x="3" y="5" width="18" height="14" rx="2"/></svg>
          corvane paintless dent removal
        </li>
      </ul>
    </div>

    <p class="holder-name">Dale Hollister</p>
  </section>

  <section class="card card-back">
    <div class="brand-name">
      <span class="brand-main">CORVANE</span>
      <span class="brand-sub">Paintless Dent Removal</span>
    </div>
    <p class="web-address">www.corvanepdr.example</p>
  </section>

</main>
</body>
</html>
```